A4 advert for Tradewick Post editorial offer

I am the publisher of online site www.tradeledgerhub.co.uk, as part of the commercial parts of the website I sell commercial licenses to PR people and marketeers who want to publish editorials onto my site.
I want an A4 visual flyer to help me send to people that have enquired about this offering. At the moment I send a simple emial with screen shots. I do however have a media pack for other advertising parts of the digital newspaper. I will upload this as part of the project to help give you an idea of how the online paper works.
Okay here is the content for the flyer..
Publish content directly onto the Tradewick Post server
The price is £250 per year paid by electronic direct debit.
As part of your membership you get the following:
Create and publish articles on Tradewick Post
Include hyperlinks back to your own website
A free company report page (similar to knowpedix)
Social logins - Allows you to sync your social media to your published articles, we also add you to our social media feeds which means as your articles are published we tweet them and send them to worknet
Create and publish blogs
Upload resources or guides to our resource library

```html
<!DOCTYPE html>
<html lang="en">
<head>
<meta charset="utf-8">
<title>Tradewick Post – Editorial Membership Flyer</title>
<link rel="stylesheet" href="https://fonts.googleapis.com/css2?family=Anton&family=Arimo:ital,wght@0,400;1,700&family=Cinzel:wght@400;700&display=swap">
<style>
  :root {
    --canvas: #e4e5e7;
    --paper: #f7f7f8;
    --navy: #1e2d5c;
    --ink: #151515;
    --maroon-light: #a51d4d;
    --maroon: #7c1039;
    --maroon-deep: #660c2f;
    --target-green: #8dc63f;
    --target-pale: #e8f2d8;
    --white: #ffffff;
  }
  * { margin: 0; padding: 0; box-sizing: border-box; }
  html, body { width: 1200px; height: 1000px; overflow: hidden; }
  body { background: var(--canvas); position: relative; }

  .flyer {
    position: absolute;
    left: 308px; top: 110px;
    width: 578px; height: 772px;
    background: var(--paper);
    overflow: hidden;
    box-shadow: 0 2px 6px rgba(0,0,0,0.18);
  }
  .header-band {
    position: absolute; left: 0; top: 0; width: 100%; height: 90px;
    background: linear-gradient(to bottom, #dcdde0 0%, var(--paper) 100%);
  }
  .brand {
    position: absolute; left: 47px; top: 55px;
    display: flex; align-items: center; gap: 8px;
  }
  .brand-dot {
    width: 30px; height: 30px; border-radius: 50%;
    border: 2px solid #8c8f96;
  }
  .brand-name {
    font-family: "Cinzel", serif; font-weight: 700;
    font-size: 28px; color: var(--navy);
  }
  .target-art {
    position: absolute; left: 322px; top: 55px;
    width: 215px; height: 160px;
    border-radius: 50%;
    background: radial-gradient(ellipse 40% 48% at 72% 50%, var(--target-green) 0%, var(--target-pale) 55%, rgba(247,247,248,0) 100%);
  }
  .headline {
    position: absolute; left: 50px; top: 183px;
    font-family: "Cinzel", serif; font-weight: 400;
    color: var(--navy); line-height: 1.15;
  }
  .headline .lead { display: block; font-size: 21px; }
  .headline .main { display: block; font-size: 31px; margin-top: 4px; }

  .benefits {
    position: absolute; left: 51px; top: 307px;
    font-family: "Arimo", sans-serif; color: var(--ink);
    font-size: 12.6px; line-height: 17px;
  }
  .benefits .intro { font-weight: 700; font-style: italic; font-size: 13px; margin-bottom: 1px; }
  .benefits p + p { margin-top: 9px; }
  .benefits .intro + p { margin-top: 1px; }

  .price-panel { position: absolute; left: 0; top: 0; width: 578px; height: 772px; }

  .price {
    position: absolute; left: 220px; top: 585px; width: 340px;
    text-align: center; color: var(--white);
    font-family: "Arimo", sans-serif;
  }
  .price .label { font-size: 26.5px; line-height: 1; }
  .price .amount {
    font-family: "Anton", sans-serif; font-size: 80px; line-height: 1;
    margin-top: 4px; letter-spacing: 3px;
  }
  .price .terms { font-size: 21px; margin-top: 0; }
</style>
</head>
<body>
  <main class="flyer">
    <div class="header-band"></div>

    <div class="brand">
      <span class="brand-dot"></span>
      <span class="brand-name">Tradewick Post</span>
    </div>

    <div class="target-art" role="img" aria-label="Illustration of an arrow hitting the centre of a green archery target"></div>

    <h1 class="headline">
      <span class="lead">Publish content directly onto</span>
      <span class="main">the Tradewick Post<br>server</span>
    </h1>

    <section class="benefits">
      <p class="intro">As part of your membership you get the following:</p>
      <p>Create and publish articles on Tradewick Post<br>
         Include hyperlinks back to your own website<br>
         A free company report page (similar to knowpedix)</p>
      <p>Social logins - Allows you to sync your social media to your<br>
         published articles, we also add you to our social media<br>
         feeds which means as your articles are published we<br>
         tweet them and send them to worknet Create and<br>
         publish blogs<br>
         Upload resources or guides to our resource<br>
         library</p>
    </section>

    <svg class="price-panel" viewBox="0 0 578 772" aria-hidden="true">
      <defs>
        <radialGradient id="maroonGlow" cx="390" cy="480" r="330" gradientUnits="userSpaceOnUse">
          <stop offset="0" stop-color="#a51d4d"/>
          <stop offset="0.55" stop-color="#7c1039"/>
          <stop offset="1" stop-color="#660c2f"/>
        </radialGradient>
        <filter id="edgeShadow" x="-20%" y="-20%" width="140%" height="140%">
          <feDropShadow dx="-4" dy="2" stdDeviation="5" flood-color="#000" flood-opacity="0.3"/>
        </filter>
      </defs>
      <polygon points="578,205 578,772 155,772" fill="url(#maroonGlow)" filter="url(#edgeShadow)"/>
    </svg>

    <div class="price">
      <p class="label">The price is</p>
      <p class="amount">£250</p>
      <p class="terms">paid by electronic direct debit</p>
    </div>
  </main>
</body>
</html>
```